Velvet Lantern rebranding my business with a new business card

I have my new logo and now I need a refresher on my business cards. I really want something fun and fresh. I like black background or anything to make the color pop.
Logo
Name: Velvet Lantern
Contact Info as stated below:
Mira Pellow
555-013-4762
Logo
Name: Velvet Lantern
Mira Pellow
555-013-4762
fb.me/VelvetLanternbyMira
Instagram: @VelvetLanternbyMira

Industry/Entity Type

Business

Contact Information for Business Card

double-sided. Logo on one side. Contact info on the other.

Requirements
Must have
• Logo
• Name: Velvet Lantern
• Contact Info as stated below:
• Mira Pellow
• 555-013-4762
• fb.me/VelvetLanternbyMira
• fb.me/VelvetLanternbyMira

```html
<!DOCTYPE html>
<html lang="en">
<head>
<meta charset="utf-8">
<title>Velvet Lantern – Business Card</title>
<link href="https://fonts.googleapis.com/css2?family=Short+Stack&display=swap" rel="stylesheet">
<style>
  :root {
    --stage: #4d4d4d;
    --card-pink: #f7bfc2;
    --badge-white: #ffffff;
    --ink: #111111;
    --ring-pink: #f2a3ad;
    --logo-rose: #c0466a;
  }
  html, body {
    margin: 0;
    padding: 0;
    width: 1200px;
    height: 849px;
    overflow: hidden;
    background: var(--stage);
  }
  .stage {
    position: relative;
    width: 1200px;
    height: 849px;
    font-family: "Short Stack", "Comic Sans MS", cursive;
    color: var(--ink);
  }
  .card {
    position: absolute;
    background: var(--card-pink);
  }
  .card-front { left: 162px; top: 274px; width: 498px; height: 300px; }
  .card-back  { left: 700px; top: 175px; width: 301px; height: 498px; }

  .badge {
    position: absolute;
    width: 198px;
    height: 198px;
    border-radius: 50%;
    background: var(--badge-white);
    border: 2px solid var(--ink);
    box-sizing: border-box;
    display: flex;
    align-items: center;
    justify-content: center;
  }
  .badge::before {
    content: "";
    position: absolute;
    inset: 5px;
    border-radius: 50%;
    border: 1.5px solid var(--ring-pink);
  }
  .card-front .badge { left: 150px; top: 51px; }
  .card-back .badge  { left: 51px;  top: 55px; }

  .brand-name {
    font-size: 22px;
    line-height: 1.15;
    text-align: center;
    color: var(--logo-rose);
    font-weight: 400;
    margin: 0;
  }

  .holder-name {
    position: absolute;
    left: 0; right: 0;
    top: 300px;
    margin: 0;
    text-align: center;
    font-size: 30px;
    font-weight: 400;
  }
  .contact-icon {
    position: absolute;
    left: 0;
    width: 301px;
    height: 22px;
  }
  .contact-icon.phone { top: 346px; }
  .contact-icon.social { top: 400px; }
  .contact-text {
    position: absolute;
    left: 0; right: 0;
    margin: 0;
    text-align: center;
  }
  .contact-text.phone  { top: 374px; font-size: 16px; }
  .contact-text.social { top: 424px; font-size: 17px; }
</style>
</head>
<body>
<main class="stage">
  <section class="card card-front" aria-label="Card front">
    <div class="badge">
      <p class="brand-name">Velvet<br>Lantern</p>
    </div>
  </section>

  <section class="card card-back" aria-label="Card back">
    <div class="badge">
      <p class="brand-name">Velvet<br>Lantern</p>
    </div>

    <h1 class="holder-name">Mira Pellow</h1>

    <svg class="contact-icon phone" viewBox="0 0 301 22" aria-hidden="true">
      <path d="M92 12 q10 -4 20 -1 q10 3 20 -1" fill="none" stroke="#111" stroke-width="1"/>
      <path d="M169 11 q10 -4 20 -1 q10 3 20 1" fill="none" stroke="#111" stroke-width="1"/>
      <rect x="141" y="2" width="19" height="19" rx="4" fill="none" stroke="#111" stroke-width="1.5"/>
      <path d="M146 6.5 q-1 5 3.5 9.5 q4.5 4 9 3 l0.5 -2.5 l-3 -1.5 l-1.5 1.5 q-3.5 -1.5 -5 -5 l1.5 -1.5 l-1.5 -3 z" fill="#111"/>
    </svg>
    <p class="contact-text phone">555-013-4762</p>

    <svg class="contact-icon social" viewBox="0 0 301 22" aria-hidden="true">
      <path d="M92 12 q10 -4 20 -1 q10 3 20 -1" fill="none" stroke="#111" stroke-width="1"/>
      <path d="M169 11 q10 -4 20 -1 q10 3 20 1" fill="none" stroke="#111" stroke-width="1"/>
      <rect x="141" y="2" width="19" height="19" rx="4" fill="none" stroke="#111" stroke-width="1.5"/>
    </svg>
    <p class="contact-text social">VelvetLanternbyMira</p>
  </section>
</main>
</body>
</html>
```